Moxy Fen needs some awesome stationary

Do you have what it takes to get my brand? You either do or you don't, have a crack at a design and you my just win my business.

I don't want to waste your or my time, so put your creative genius on either a business card or envelope.

I however need a package of stationary that follows the same brand. I will message you to complete the remaining should I like your first submission.

Here is what I need, have a go!

Basically I need the following for my small business based in melbourne.
- Letterhead (printer ready and MS Word)
- Business Card
- Compliments Slip
- Envelope
- Proposal Cover Page (MS Word only)
- Presentation Folder
- Marbled Fox Cards
- Student Name Tent
- Index Cards
- Vell-Ka

I am establishing the brand and it must be modern, professional but also relaxed; that is not formal and not corporate. It represents a company are leaders, but small enough to care and operate like a bunch of friends. We are bringing people and conversations back to business, and turfing out all the bureaucracy and crazy and wasteful procedures. Its about "lets talk and figure it out together and find even better ways".

Target Market(s)

Mainly companies that build software products, but Agile practices are used in many other industries (even graphic design projects)

Industry/Entity Type

Information Technology

Font styles to use
Sans Serif

Colors
3176b5
aaaaaa

Requirements
Must have
• I like curves and circles and not boxes or rectangles.
• I want a colour rich design with my brand colours, but it must be balanced.
• I want more modern than traditional, but simple modern
Should not have
• Not corporate
• Please don't waste my time if your not going to think about it.
• Don't mess with my primary logo
• Don't change my colours
• Don't overlay logo on image

```html
<!DOCTYPE html>
<html lang="en">
<head>
<meta charset="utf-8">
<title>Moxy Fen – Envelope</title>
<link href="https://fonts.googleapis.com/css2?family=Open+Sans:wght@400;700&display=swap" rel="stylesheet">
<style>
  :root {
    --stage: #8a8b8f;
    --paper: #ffffff;
    --brand-blue: #3176b5;
    --flap-blue: #416ba9;
    --brand-grey: #aaaaaa;
    --ink: #555a60;
    --faint: #f3f5f8;
  }
  * { margin: 0; padding: 0; box-sizing: border-box; }
  html, body {
    width: 1200px; height: 1059px; overflow: hidden;
    background: var(--stage);
    font-family: "Open Sans", Arial, sans-serif;
  }
  .canvas { position: relative; width: 1200px; height: 1059px; }
  .envelope {
    position: absolute; left: 140px; width: 897px; height: 428px;
    background: var(--paper);
    box-shadow: 0 1px 4px rgba(0,0,0,0.35);
    overflow: hidden;
  }
  .envelope--front { top: 85px; }
  .envelope--back { top: 556px; }
  .front-decor { position: absolute; inset: 0; }
  .sender { position: absolute; left: 51px; top: 45px; }
  .brand-name {
    display: flex; align-items: center; gap: 10px;
    font-weight: 700; font-size: 25px; color: var(--brand-blue);
    letter-spacing: -0.2px;
  }
  .brand-dot {
    width: 22px; height: 22px; border-radius: 50%;
    background: var(--brand-blue);
  }
  .sender-address {
    margin-top: 56px;
    font-style: normal; font-size: 12.2px; line-height: 15.5px;
    color: var(--ink);
  }
  .flap { position: absolute; left: 0; top: 0; width: 897px; height: 152px; }
  .flap-brand {
    position: absolute; left: 0; right: 0; top: 42px;
    text-align: center; color: var(--paper);
  }
  .flap-brand .brand-name {
    justify-content: center; color: var(--paper); font-size: 19px; gap: 8px;
  }
  .flap-brand .brand-dot { width: 16px; height: 16px; background: var(--paper); }
  .web-address { margin-top: 8px; font-size: 11.5px; letter-spacing: 0.1px; }
</style>
</head>
<body>
<main class="canvas">
  <section class="envelope envelope--front" aria-label="Envelope front">
    <svg class="front-decor" width="897" height="428" viewBox="0 0 897 428" aria-hidden="true">
      <circle cx="587" cy="211" r="244" fill="var(--faint)"/>
    </svg>
    <div class="sender">
      <div class="brand-name"><span class="brand-dot"></span>Moxy Fen</div>
      <address class="sender-address">
        PO Box 4817<br>
        Eltham North<br>
        VIC 3095, Australia
      </address>
    </div>
  </section>

  <section class="envelope envelope--back" aria-label="Envelope back">
    <svg class="flap" width="897" height="152" viewBox="0 0 897 152" aria-hidden="true">
      <path d="M0 0 H897 L884 130 Q881 146 864 147 L33 150 Q17 150 15 134 Z" fill="var(--flap-blue)"/>
    </svg>
    <div class="flap-brand">
      <div class="brand-name"><span class="brand-dot"></span>Moxy Fen</div>
      <p class="web-address">www.moxy-fen.com.au</p>
    </div>
  </section>
</main>
</body>
</html>
```